SANDWICH SKILLET DESIGN (Packaging)

We require a skillet (sandwich box) designed I have uploaded a similar one we have already
I have uploaded the logo to be placed on the skillet
( BRIGHT MEADOW DELI HAWKS LTD)
we would like a sandwich skillet which has a white background and maybe some veg items which maybe found in a sandwich
hope this helps

```html
<!DOCTYPE html>
<html lang="en">
<head>
<meta charset="utf-8">
<title>Bright Meadow Deli – Sandwich Skillet</title>
<link rel="stylesheet" href="https://fonts.googleapis.com/css2?family=Archivo:ital,wght@0,600;0,800;1,800&display=swap">
<style>
  :root {
    --brand-red: #9b0d10;
    --wood-light: #eeece8;
    --wood-mid: #dcd9d3;
    --ink: #1b1b1b;
    --paper: #ffffff;
    --stage: #e6e6e6;
  }
  * { box-sizing: border-box; margin: 0; padding: 0; }
  html, body { width: 1200px; height: 720px; overflow: hidden; }
  body {
    background: var(--stage);
    font-family: "Archivo", Arial, sans-serif;
    position: relative;
  }
  .panel {
    position: absolute;
    top: 90px;
    height: 540px;
    background:
      repeating-linear-gradient(90deg, transparent 0 9px, rgba(0,0,0,0.035) 9px 10px, transparent 10px 23px),
      linear-gradient(90deg, var(--wood-light), var(--wood-mid) 55%, var(--wood-light));
    overflow: hidden;
  }

  /* Front panel */
  .front-panel { left: 130px; width: 300px; }
  .notice-band {
    position: absolute;
    left: 24px; right: 0;
    height: 30px;
    display: flex; align-items: center; justify-content: center;
    font-weight: 800; font-style: italic;
    font-size: 13.5px; letter-spacing: 0.3px;
  }
  .notice-band--red { background: var(--brand-red); color: var(--paper); }
  .notice-band--white { background: var(--paper); color: var(--brand-red); }
  .notice-band:nth-child(1) { top: 18px; }
  .notice-band:nth-child(2) { top: 48px; }
  .notice-band:nth-child(3) { top: 78px; }
  .product-window {
    position: absolute;
    left: 24px; top: 128px;
    width: 252px; height: 270px;
    border-radius: 4px;
    background: linear-gradient(160deg, #8a9a5b 0%, #b98c86 30%, #c9a398 50%, #9bbf6a 72%, #e6ded1 100%);
  }
  .brand-seal {
    position: absolute;
    left: 50%; bottom: 18px;
    transform: translateX(-50%);
    width: 116px; height: 116px;
  }
  .brand-seal__ribbon {
    position: absolute;
    left: 50%; bottom: -18px;
    transform: translateX(-50%);
    width: 86px; height: 70px;
    background: var(--brand-red);
  }
  .brand-seal__disc {
    position: absolute; inset: 0;
    border-radius: 50%;
    background: var(--paper);
    border: 3px solid var(--brand-red);
    display: flex; align-items: center; justify-content: center;
    text-align: center;
  }
  .brand-name {
    color: var(--brand-red);
    font-weight: 600;
    font-size: 11px;
    line-height: 1.3;
    letter-spacing: 0.4px;
  }

  /* Side panel */
  .side-panel { position: absolute; left: 450px; top: 90px; }

  /* Back panel */
  .back-panel { left: 780px; width: 290px; }
  .ingredient-photo { position: absolute; z-index: 0; }
  .ingredient-photo--milk { left: 0; top: 370px; width: 40px; height: 70px; border-radius: 0 20px 20px 0; background: radial-gradient(circle at 30% 40%, #ffffff, #e9eef3 80%); }
  .ingredient-photo--wheat { right: 8px; top: 362px; width: 34px; height: 84px; background: linear-gradient(180deg, #d9b46b, #b98b45); border-radius: 16px 16px 4px 4px; }
  .ingredient-photo--nuts { right: 6px; bottom: 8px; width: 48px; height: 24px; background: linear-gradient(90deg, #a06a3c, #d1a574); border-radius: 12px; }
  .allergen-note {
    position: absolute; z-index: 1;
    left: 48px; right: 48px; top: 404px;
    font-size: 8.5px; font-weight: 600; color: var(--ink);
    text-align: center; line-height: 1.35;
  }
  .contact-block {
    position: absolute; z-index: 1;
    left: 88px; right: 0; top: 456px;
  }
  .contact-block__company {
    background: var(--brand-red); color: var(--paper);
    font-weight: 800; font-size: 8.5px;
    text-align: center; padding: 7px 4px; line-height: 1.4;
  }
  .contact-block__email {
    background: var(--paper); color: var(--brand-red);
    font-weight: 800; font-size: 8.5px;
    text-align: center; padding: 7px 4px;
  }
  .back-seal {
    position: absolute; z-index: 2;
    left: 10px; top: 448px;
    width: 74px; height: 74px;
    border-radius: 50%;
    background: var(--paper);
    border: 2px solid var(--brand-red);
    display: flex; align-items: center; justify-content: center; text-align: center;
  }
  .back-seal .brand-name { font-size: 7px; }
</style>
</head>
<body>

  <section class="panel front-panel" aria-label="Front panel">
    <div class="notice-stack">
      <div class="notice-band notice-band--red">FRESHLY HANDMADE SANDWICH</div>
      <div class="notice-band notice-band--white">EAT ONE DAY OF PURCHASE</div>
      <div class="notice-band notice-band--red">KEEP REFRIGERATED BELOW 5 C</div>
    </div>
    <div class="product-window" role="img" aria-label="Clear window showing a ham, cheese and lettuce sandwich"></div>
    <div class="brand-seal">
      <div class="brand-seal__ribbon"></div>
      <div class="brand-seal__disc">
        <p class="brand-name">BRIGHT MEADOW<br>DELI HAWKS LTD</p>
      </div>
    </div>
  </section>

  <svg class="side-panel" width="310" height="540" viewBox="0 0 310 540" aria-label="Side panel">
    <defs>
      <linearGradient id="wood-fill" x1="0" x2="1">
        <stop offset="0" stop-color="#dcd9d3"/>
        <stop offset="1" stop-color="#eeece8"/>
      </linearGradient>
      <radialGradient id="salad-fill" cx="0.62" cy="0.62" r="0.62">
        <stop offset="0" stop-color="#8cc94a"/>
        <stop offset="0.55" stop-color="#6aac34"/>
        <stop offset="0.85" stop-color="#9fcf6a"/>
        <stop offset="1" stop-color="#c9e3a6"/>
      </radialGradient>
      <clipPath id="side-clip">
        <polygon points="310,0 310,540 0,540"/>
      </clipPath>
    </defs>
    <polygon class="side-panel__board" points="310,0 310,540 0,540" fill="url(#wood-fill)"/>
    <g clip-path="url(#side-clip)">
      <path class="side-panel__salad" role="img" aria-label="Photo of fresh salad: cheese, cucumber, olives, tomato, onion, lime and peppers"
            d="M310,150 C280,150 262,190 250,230 C222,262 200,300 190,340 C160,370 140,410 128,440 C100,470 80,500 70,540 L310,540 Z"
            fill="url(#salad-fill)"/>
    </g>
  </svg>

  <section class="panel back-panel" aria-label="Back panel">
    <div class="ingredient-photo ingredient-photo--milk" role="img" aria-label="Milk splash photo"></div>
    <div class="ingredient-photo ingredient-photo--wheat" role="img" aria-label="Wheat ears photo"></div>
    <div class="ingredient-photo ingredient-photo--nuts" role="img" aria-label="Mixed nuts photo"></div>
    <p class="allergen-note">May contain lupin, molluscs, milk, barley, sesame seeds, crustaceans, fish, sulphites, soya, cellery &amp; nuts</p>
    <div class="contact-block">
      <p class="contact-block__company">BRIGHT MEADOW DELI HAWKS LTD<br>UNIT 4 ALDER LANE HK3 7PL</p>
      <p class="contact-block__email">HELLO@BRIGHTMEADOW.CO.UK</p>
    </div>
    <div class="back-seal">
      <p class="brand-name">BRIGHT MEADOW<br>DELI HAWKS</p>
    </div>
  </section>

</body>
</html>
```